Business Card for Vorla Parts Wholesale supplier

Hi There! I need a new business card for our company. We are specialized in selling Vorla parts, mostly we sell new LCD screens for Zelnar and Drelks. I would like to see that back in the design.

You can find the colors and logo's on our website: www.hartuvo.nl

Industry/Entity Type

Business

Contact Information for Business Card

My Details:
Tobias Lindqvist

Phone: 0031687203316
E-mail: Tobias@hartuvo.nl

Slogan: "Because Quality Matters"

Font styles to use
Sans Serif

Colors

Designer to choose colors to be used in the design.

Requirements
Must have
• A Black backside with the Hartuvo logo on it. The front side should be clean with only my contact details.
• But I'm also open for something really different or awesome!
Nice to have
• Remember that we are in the parts & repairing industry, So i'll be handing those business cards mainly to repair companies. Maybe you can do something with that thought :)

```html
<!DOCTYPE html>
<html lang="en">
<head>
<meta charset="utf-8">
<title>Hartuvo Business Card</title>
<link href="https://fonts.googleapis.com/css2?family=Open+Sans:wght@400;600;700;800&display=swap" rel="stylesheet">
<style>
  :root {
    --stage: #2b2b2d;
    --card-dark: #1c1d20;
    --card-dark-tint: #24252a;
    --card-light: #ffffff;
    --brand-orange: #f07022;
    --faint-peach: #fdf1ea;
    --ink: #111111;
    --paper-text: #ffffff;
  }
  * { box-sizing: border-box; margin: 0; padding: 0; }
  html, body {
    width: 1200px;
    height: 1189px;
    overflow: hidden;
  }
  body {
    background: var(--stage);
    font-family: "Open Sans", Arial, sans-serif;
    position: relative;
  }
  .card {
    position: absolute;
    left: 150px;
    width: 900px;
    height: 514px;
    border-radius: 34px;
    overflow: hidden;
    box-shadow: 0 18px 40px rgba(0,0,0,0.45);
  }
  /* Back side */
  .card-back {
    top: 54px;
    background: var(--card-dark);
  }
  .card-back .backdrop-shape {
    position: absolute;
    left: 230px;
    top: -60px;
    width: 520px;
    height: 520px;
    border-radius: 50%;
    background: var(--card-dark-tint);
  }
  .card-back .brand {
    position: absolute;
    left: 0;
    right: 0;
    top: 50%;
    transform: translateY(-50%);
    display: flex;
    align-items: center;
    justify-content: center;
    gap: 22px;
  }
  .brand-dot {
    width: 68px;
    height: 68px;
    border-radius: 50%;
    background: var(--brand-orange);
  }
  .card-back .brand-name {
    font-weight: 800;
    font-size: 104px;
    letter-spacing: 2px;
    color: var(--paper-text);
    line-height: 1;
  }
  /* Front side */
  .card-front {
    top: 622px;
    background: var(--card-light);
  }
  .card-front .backdrop-shape {
    position: absolute;
    right: -90px;
    top: -20px;
    width: 520px;
    height: 520px;
    border-radius: 50%;
    background: var(--faint-peach);
  }
  .card-front .brand {
    position: absolute;
    left: 66px;
    top: 70px;
    display: flex;
    align-items: center;
    gap: 20px;
  }
  .card-front .brand-dot {
    width: 76px;
    height: 76px;
  }
  .card-front .brand-name {
    font-weight: 800;
    font-size: 96px;
    letter-spacing: 2px;
    color: var(--ink);
    line-height: 1;
  }
  .contact {
    position: absolute;
    left: 92px;
    top: 262px;
  }
  .contact-name {
    font-weight: 700;
    font-size: 32px;
    color: var(--brand-orange);
    letter-spacing: 0.5px;
    margin-bottom: 22px;
  }
  .contact-line {
    font-size: 24px;
    color: var(--ink);
    line-height: 1.35;
  }
  .contact-line .label {
    font-weight: 700;
    color: var(--brand-orange);
  }
  .contact-line .accent { color: var(--brand-orange); }
  .slogan {
    margin-top: 24px;
    font-weight: 800;
    font-size: 26px;
    color: var(--ink);
  }
</style>
</head>
<body>
  <section class="card card-back" aria-label="Card back">
    <div class="backdrop-shape"></div>
    <div class="brand">
      <span class="brand-dot"></span>
      <span class="brand-name">Hartuvo</span>
    </div>
  </section>

  <section class="card card-front" aria-label="Card front">
    <div class="backdrop-shape"></div>
    <div class="brand">
      <span class="brand-dot"></span>
      <span class="brand-name">Hartuvo</span>
    </div>
    <div class="contact">
      <p class="contact-name">Tobias Lindqvist</p>
      <p class="contact-line"><span class="label">P:</span> 0031687203316</p>
      <p class="contact-line"><span class="label">E:</span> Tobias@hartuvo.nl</p>
      <p class="contact-line">www.<span class="accent">hartuvo</span>.nl</p>
      <p class="slogan">Because Quality Matters</p>
    </div>
  </section>
</body>
</html>
```